Website design for Puddle Jump Kidscare

I need a website designed for my daycare business, Puddle Jump Kidscare, now that I have a new logo. My former website was ok but simple and I did not have a logo yet. It also was created by me using a template and was entirely pink. I loved the bright, happy feel of it but worried it might not appeal as much to potential clients who have sons. Therefore, I need a site which will appeal to both genders while still keeping the cheerful color scheme of my new logo, which has pinks, blue, green and cream.
Updates

Reason: Hello! I am still trying to download my new logo and am sorry it is taking me so long. Hopefully I will it posted by the end of today (US Eastern Standard Time). Thank you all very much for your patience!

Hello! I have finally managed to upload my new logo for you to use in designing my website. I'm sorry it took so long and greatly appreciate your time and creative efforts! I look forward to seeing what is submitted based on my logo design and its style/colors.

Many thanks!

Reason: As I've been traveling and posted my logo file late, I am extending my deadline. I am now back and can focus on providing more and better feedback. I appreciate your patience and submissions very much!

Reason: I need more time to provide feedback and make decisions.

Industry/Entity Type

Daycare

Colors
0192cd
33a6d7
86cae7
cadf82
fbf289
add136
e34197

```html
<!DOCTYPE html>
<html lang="en">
<head>
<meta charset="utf-8">
<title>About Us – Puddle Jump Kidscare</title>
<link href="https://fonts.googleapis.com/css2?family=Source+Sans+3:wght@400;600&display=swap" rel="stylesheet">
<style>
:root{
  --pink:#e0306f;
  --pink-soft:#f39ac4;
  --green:#8cc63f;
  --green-box:#a1d14a;
  --green-bar:#b8d65c;
  --brown:#7a5230;
  --brown-head:#6b4a2e;
  --text:#7f8ea3;
  --muted:#9aa6b5;
  --blue-link:#3aa5d6;
  --line:#e6e8ea;
  --footer-bg:#f7f7f5;
  --page:#fcfdfd;
}
*{margin:0;padding:0;box-sizing:border-box}
html,body{width:1027px;height:1200px;overflow:hidden}
body{position:relative;background:var(--page);font-family:"Source Sans 3",sans-serif;color:var(--text)}
.abs{position:absolute}

/* header */
.brand{left:136px;top:48px;display:flex;align-items:center;gap:10px}
.brand-dot{width:26px;height:26px;border-radius:50%;background:var(--pink-soft);flex:none}
.brand-name{font-size:25px;font-weight:600;color:var(--pink);line-height:1}
.contact-strip{top:43px;left:428px;display:flex;height:40px;align-items:center;font-size:11px;color:var(--text)}
.contact-item{display:flex;align-items:center;gap:9px;height:40px;border-left:1px solid var(--line);padding:0 14px 0 16px}
.contact-item svg{flex:none}
.main-nav{top:133px;left:0;width:1027px;height:33px}
.main-nav ul{list-style:none}
.main-nav li{position:absolute;top:0;font-size:13px;color:var(--pink)}
.main-nav li.active{color:var(--green);font-weight:600}
.nav-bar{top:161px;left:0;width:1027px;height:5px;background:var(--pink)}
.nav-active-mark{top:160px;left:237px;width:63px;height:6px;background:var(--green)}
.nav-active-mark::after{content:"";position:absolute;left:27px;top:-4px;border:4px solid transparent;border-top:0;border-bottom-color:var(--green)}

/* content */
.page-title{left:139px;top:196px;font-size:29px;font-weight:400;color:var(--green)}
.hero-photo{left:136px;top:249px;width:433px;height:166px;border-radius:8px;
  background:linear-gradient(100deg,#f2e6c6 0%,#c99a62 22%,#9b6b3e 45%,#c7955c 68%,#f0dbb5 100%)}
.intro{left:141px;top:434px;width:440px;font-size:14.5px;line-height:24px;color:var(--brown)}
.body-copy{left:141px;top:496px;width:445px;font-size:12px;line-height:16.8px;color:var(--text)}
.body-copy p+p{margin-top:17px}
.sidebar-rule{left:633px;top:210px;width:1px;height:648px;background:var(--line)}

/* sidebar */
.side-head{position:absolute;font-size:14px;font-weight:400;color:var(--brown-head)}
.news{position:absolute;left:654px;display:flex;gap:17px;width:240px}
.news-date{flex:none;width:47px;height:47px;background:var(--pink-soft);color:#fff;text-align:center;padding-top:5px}
.news-date b{display:block;font-weight:400;font-size:17px;line-height:18px}
.news-date span{font-size:7px}
.news-text{width:168px;font-size:10.5px;line-height:16px;color:var(--text);margin-top:-2px}
.read-more{font-size:7.5px;font-weight:600;color:var(--blue-link);margin-left:6px}
.avatar{left:657px;top:423px;width:40px;height:40px;background:linear-gradient(135deg,#c68d62,#7b5a43)}
.person-name{left:706px;top:422px;font-size:14px;color:#556170}
.person-role{left:707px;top:445px;font-size:9px;color:var(--muted)}
.quote-box{left:657px;top:479px;width:199px;height:87px;background:var(--green-box);padding:18px 13px 0 32px;
  font-size:9.5px;line-height:16px;font-weight:600;color:#fff;text-align:justify}
.quote-box::before{content:"";position:absolute;left:14px;top:-10px;border-right:12px solid transparent;border-bottom:10px solid var(--green-box)}
.quote-mark{position:absolute;left:11px;top:10px;font-size:24px;line-height:1}

/* footer */
.site-footer{left:0;top:999px;width:1027px;height:164px;background:var(--footer-bg);border-top:1px solid var(--line)}
.footer-brand{left:140px;top:1055px;width:150px;display:flex;align-items:center;gap:8px}
.footer-brand .brand-name{font-size:19px;line-height:22px}
.footer-brand .brand-dot{width:20px;height:20px}
.foot-col{position:absolute;top:1029px}
.foot-col h4{font-size:10.5px;font-weight:600;color:#9b8a78;margin-bottom:9px}
.foot-list{list-style:none;font-size:9.5px;color:var(--text);letter-spacing:.3px}
.foot-list li{height:19.2px;padding-left:10px;position:relative}
.foot-list li::before{content:"";position:absolute;left:0;top:3px;border:3px solid transparent;border-left:3px solid #c5cbd2;border-right:0}
.foot-list li.current{color:var(--green)}
.foot-contact{list-style:none;font-size:9.5px;color:var(--text)}
.foot-contact li{display:flex;gap:9px;line-height:19px;margin-bottom:5px}
.foot-contact svg{flex:none;margin-top:3px}
.map{left:717px;top:1052px;width:174px;height:82px;background:linear-gradient(135deg,#e4e2dc,#d9dbd8 50%,#bcc9d6)}
.bottom-bar{left:0;top:1163px;width:1027px;height:37px;background:var(--green-bar);color:#fff;font-size:10px}
.bottom-bar .copy{position:absolute;left:136px;top:12px}
.bottom-bar .legal{position:absolute;right:141px;top:12px;display:flex;gap:9px}
</style>
</head>
<body>

<header>
  <div class="brand abs"><span class="brand-dot"></span><span class="brand-name">Puddle Jump Kidscare</span></div>
  <div class="contact-strip abs">
    <div class="contact-item">
      <svg width="16" height="16" viewBox="0 0 16 16"><circle cx="8" cy="9" r="5.5" fill="none" stroke="#e0306f" stroke-width="1.6"/><path d="M8 6v3.3l2 1.2" stroke="#e0306f" stroke-width="1.4" fill="none"/><path d="M2 4l2.5-2M14 4l-2.5-2" stroke="#e0306f" stroke-width="1.5"/></svg>
      <span>(Mon - Fri) 8:00AM to 6:00PM</span>
    </div>
    <div class="contact-item">
      <svg width="24" height="12" viewBox="0 0 24 12"><path d="M0 2h6M2 5h4M4 8h2" stroke="#e0306f" stroke-width="1"/><rect x="8" y="1" width="15" height="10" fill="none" stroke="#e0306f" stroke-width="1.4"/><path d="M8 1l7.5 6 7.5-6" fill="none" stroke="#e0306f" stroke-width="1.3"/></svg>
      <span>hello@puddlejumpkids.com</span>
    </div>
    <div class="contact-item">
      <svg width="15" height="15" viewBox="0 0 15 15"><path d="M3 1l3 3-1.5 2a8 8 0 0 0 4.5 4.5l2-1.5 3 3-2 2C6 13 2 9 1 3z" fill="#e0306f"/></svg>
      <span>+(555) 204-7731</span>
    </div>
  </div>
  <nav class="main-nav abs">
    <ul>
      <li style="left:165px">Home</li>
      <li class="active" style="left:250px">About</li>
      <li style="left:329px">Services</li>
      <li style="left:418px">Hours &amp; Fees</li>
      <li style="left:534px">Policies</li>
      <li style="left:620px">Photos</li>
      <li style="left:702px">Testimonials</li>
      <li style="left:816px">Contact Us</li>
    </ul>
  </nav>
  <div class="nav-bar abs"></div>
  <div class="nav-active-mark abs"></div>
</header>

<main>
  <h1 class="page-title abs">About Us</h1>
  <div class="hero-photo abs" role="img" aria-label="Photo of three smiling children close together"></div>
  <p class="intro abs">Puddle Jump Kidscare was founded by a busy mother who loves caring for and working with children!</p>
  <div class="body-copy abs">
    <p>After the birth of her own daughter and years of feeling challenged with and hearing other parents' frustration over not being able to find reliable, affordable, part-time child-care, she decided to create a space which would allow her to help others like her in similar situations. Whether needing full-time care, help before or after school, or simply wanting a few hours during the day to run errands, she longed to create a better option than having to pay child care providers premium rates to work limited days or hours. In her efforts to provide a better solution, a flexible, affordable, and enriching play space was born in which small groups of children are not only given top quality hands-on care in a nurturing, home-like environment, but given fun creative opportunities to learn new skills and make new friends.</p>
    <p>Puddle Jump Kidscare is fully licensed by Lakeshore State's Office of Child and Family Services and is staffed with highly qualified and trained care-takers who have undergone extensive background checks and Pediatric/Adult CPR and First Aid certification. We have a very small caregiver: child ratio and pride ourselves on giving each child the individual and special attention they deserve</p>
  </div>
  <div class="sidebar-rule abs"></div>

  <aside>
    <h3 class="side-head" style="left:654px;top:207px">Latest News</h3>
    <article class="news" style="top:243px">
      <div class="news-date"><b>05</b><span>May 2014</span></div>
      <p class="news-text">We are thrilled to have found a new cheerful space with a private backyard... <span class="read-more">▸READ MORE</span></p>
    </article>
    <article class="news" style="top:316px">
      <div class="news-date"><b>05</b><span>May 2014</span></div>
      <p class="news-text">We are thrilled to have found a new cheerful space with a private backyard... <span class="read-more">▸READ MORE</span></p>
    </article>

    <h3 class="side-head" style="left:654px;top:396px">Testimonial</h3>
    <div class="avatar abs" role="img" aria-label="Portrait photo of the reviewer"></div>
    <div class="person-name abs">Marcus Hale</div>
    <div class="person-role abs">Businessman</div>
    <blockquote class="quote-box abs"><span class="quote-mark">“</span>Mauris urnaei elit, mattis non urna acem, ullamcorper vula putatem lorem.</blockquote>
  </aside>
</main>

<footer>
  <div class="site-footer abs"></div>
  <div class="footer-brand abs"><span class="brand-dot"></span><span class="brand-name">Puddle Jump<br>Kidscare</span></div>
  <div class="foot-col" style="left:315px">
    <h4>Navigation</h4>
    <ul class="foot-list"><li class="current">Home</li><li>About</li><li>Services</li><li>Contact</li></ul>
  </div>
  <div class="foot-col" style="left:441px">
    <h4>Links</h4>
    <ul class="foot-list"><li>Hours &amp; Fees</li><li>Policies</li><li>Testimonials</li><li>Photos</li></ul>
  </div>
  <div class="foot-col" style="left:569px">
    <h4>Contact Us</h4>
    <ul class="foot-contact">
      <li><svg width="10" height="10" viewBox="0 0 15 15"><path d="M3 1l3 3-1.5 2a8 8 0 0 0 4.5 4.5l2-1.5 3 3-2 2C6 13 2 9 1 3z" fill="#b9c1ca"/></svg><span>+1800-555-0142</span></li>
      <li><svg width="11" height="8" viewBox="0 0 11 8"><rect width="11" height="8" fill="#c8ced5"/><path d="M0 0l5.5 4.5L11 0" fill="none" stroke="#fff" stroke-width="1"/></svg><span>info@puddlejumpkids.com</span></li>
      <li><svg width="9" height="12" viewBox="0 0 9 12"><path d="M4.5 12S0 6.5 0 4.5a4.5 4.5 0 0 1 9 0C9 6.5 4.5 12 4.5 12z" fill="#c8ced5"/><circle cx="4.5" cy="4.5" r="1.6" fill="#fff"/></svg><span>Address, Your Country<br>Your Zip Code</span></li>
    </ul>
  </div>
  <div class="foot-col" style="left:718px"><h4>Visit Us</h4></div>
  <div class="map abs" role="img" aria-label="Street map showing the daycare location"></div>
  <div class="bottom-bar abs">
    <span class="copy">Copyright 2014 © Puddle Jump Kidscare - All Rights Reserved</span>
    <span class="legal"><span>Site Map</span><span>•</span><span>Privacy Policy</span></span>
  </div>
</footer>

</body>
</html>
```